Gobal construction supply company needs new business card design

I need a business card design for my global supply company using an existing logo. i will be looking to print these on rounded corner cards with the black background version of my logo on the back. on the front white background, my logo again and my simple details.

```html
<!DOCTYPE html>
<html lang="en">
<head>
<meta charset="utf-8">
<title>Meridian Supply Works – Business Cards</title>
<link rel="stylesheet" href="https://fonts.googleapis.com/css2?family=Montserrat:wght@400;500;700;800&display=swap">
<style>
  :root {
    --canvas: #2b2b2d;
    --card-dark: #1c1b1d;
    --card-dark-2: #2e2c30;
    --card-light: #ffffff;
    --brand-red: #e0232a;
    --ink: #231f20;
    --text-light: #f2f2f2;
  }
  * { box-sizing: border-box; margin: 0; padding: 0; }
  html, body { width: 1200px; height: 930px; overflow: hidden; }
  body {
    background: var(--canvas);
    font-family: "Montserrat", sans-serif;
    position: relative;
  }
  .card {
    position: absolute;
    left: 250px;
    width: 700px;
    height: 400px;
    border-radius: 26px;
    overflow: hidden;
  }
  .card--back { top: 45px; background: linear-gradient(135deg, var(--card-dark-2), var(--card-dark) 70%); }
  .card--front { top: 485px; background: linear-gradient(160deg, var(--card-dark-2), var(--card-dark) 75%); }

  .map-area {
    position: absolute;
    left: 60px; top: 50px;
    width: 580px; height: 300px;
    border-radius: 140px;
    background: radial-gradient(ellipse at center, rgba(255,255,255,0.07), rgba(255,255,255,0) 70%);
  }

  .brand {
    position: absolute;
    display: flex;
    align-items: center;
    gap: 12px;
  }
  .brand__name {
    font-weight: 800;
    letter-spacing: 1px;
    text-transform: uppercase;
    line-height: 1;
    white-space: nowrap;
  }
  .brand__dot {
    width: 22px; height: 22px;
    border-radius: 50%;
    background: var(--brand-red);
    flex: none;
  }
  .card--back .brand { left: 0; right: 0; top: 182px; justify-content: center; }
  .card--back .brand__name { color: var(--card-light); font-size: 34px; }

  .front-shape { position: absolute; inset: 0; }
  .card--front .brand { right: 40px; top: 72px; }
  .card--front .brand__dot { width: 18px; height: 18px; }
  .card--front .brand__name { color: var(--ink); font-size: 21px; }

  .contact {
    position: absolute;
    left: 46px; bottom: 36px;
    color: var(--text-light);
  }
  .contact__name {
    color: var(--brand-red);
    font-weight: 700;
    font-size: 25px;
    text-transform: uppercase;
    line-height: 1;
    white-space: nowrap;
  }
  .contact__role { font-size: 16px; margin-top: 6px; }
  .contact__address { font-size: 16px; margin-top: 14px; line-height: 1.35; }
  .contact__list { list-style: none; margin-top: 12px; font-size: 16px; line-height: 1.55; }
  .contact__list li { display: flex; align-items: center; gap: 10px; }
  .contact__list svg { width: 13px; height: 13px; flex: none; }
</style>
</head>
<body>

  <section class="card card--back" aria-label="Card back">
    <div class="map-area" role="img" aria-label="Faint dotted world map"></div>
    <div class="brand">
      <span class="brand__dot"></span>
      <span class="brand__name">Meridian Supply Works</span>
    </div>
  </section>

  <section class="card card--front" aria-label="Card front">
    <svg class="front-shape" viewBox="0 0 700 400" preserveAspectRatio="none" aria-hidden="true">
      <path d="M240 0 H700 V280 C520 290 320 200 240 0 Z" fill="var(--card-light)"/>
      <path d="M240 0 C320 200 520 290 700 280" fill="none" stroke="var(--brand-red)" stroke-width="7"/>
    </svg>

    <div class="brand">
      <span class="brand__dot"></span>
      <span class="brand__name">Meridian Supply Works</span>
    </div>

    <div class="contact">
      <p class="contact__name">Daniel Carter</p>
      <p class="contact__role">Director</p>
      <p class="contact__address">48 Harbour Road Box<br>2207, Lakeview, AB</p>
      <ul class="contact__list">
        <li>
          <svg viewBox="0 0 24 24" aria-hidden="true"><path fill="var(--brand-red)" d="M6.6 10.8a15 15 0 0 0 6.6 6.6l2.2-2.2c.3-.3.7-.4 1-.2 1.1.4 2.3.6 3.6.6.6 0 1 .4 1 1V20c0 .6-.4 1-1 1A17 17 0 0 1 3 4c0-.6.4-1 1-1h3.5c.6 0 1 .4 1 1 0 1.3.2 2.5.6 3.6.1.3 0 .7-.2 1z"/></svg>
          403-555-0182
        </li>
        <li>
          <svg viewBox="0 0 24 24" aria-hidden="true"><rect x="3" y="5" width="18" height="14" rx="1.5" fill="none" stroke="var(--brand-red)" stroke-width="2"/><path d="M3 6l9 7 9-7" fill="none" stroke="var(--brand-red)" stroke-width="2"/></svg>
          info@meridiansupply.com
        </li>
        <li>
          <svg viewBox="0 0 24 24" aria-hidden="true"><circle cx="12" cy="12" r="9" fill="none" stroke="var(--brand-red)" stroke-width="2"/><path d="M3 12h18M12 3c3 3 3 15 0 18M12 3c-3 3-3 15 0 18" fill="none" stroke="var(--brand-red)" stroke-width="1.6"/></svg>
          www.meridiansupply.com
        </li>
      </ul>
    </div>
  </section>

</body>
</html>
```